Building company buisness cards

We are looking for a sharp modern new look for our business cards.We are a New Zealand based company that specialises in house and land packages.We have attached a photo of the current logo and would like to see if it can be improved somehow if needed.We are open to any colours but we have chosen Black and White at this stage. Feel free to change the font and make the logo smarter looking.Play with the colours and see what looks best.We want a card that looks so good know one will want to throw it away!

Target Market(s)

Building profesonals, home buyers

Industry/Entity Type

Building

Contact Information for Business Card

Garrick Tenwood
0275390628
garrickt@hartvale.co.nz

Font styles to use
Serif
Sans Serif

Colors

Designer to choose colors to be used in the design.

Requirements
Must have
• Just the logo on one side and details on the other
• Clean simple looking card
Nice to have
• Round corners and detail like raised or spot UV
• Something that stands out
Should not have
• To title needed, Director etc

```html
<!DOCTYPE html>
<html lang="en">
<head>
<meta charset="utf-8">
<title>Hartvale Business Card</title>
<link rel="stylesheet" href="https://fonts.googleapis.com/css2?family=Saira:wght@400;500;600;700&display=swap">
<style>
  :root {
    --navy: #1d2858;
    --orange: #ef9a26;
    --white: #ffffff;
    --paper: #e4e4e4;
    --ink: #4a4a4a;
    --rule: #555a66;
    --silver: #dfe2e7;
  }
  * { margin: 0; padding: 0; box-sizing: border-box; }
  html, body { width: 1125px; height: 1200px; overflow: hidden; }
  body {
    background: var(--paper);
    font-family: "Saira", Arial, sans-serif;
    position: relative;
  }
  .card {
    position: absolute;
    left: 157px;
    width: 825px;
    height: 470px;
    border-radius: 28px;
    overflow: hidden;
  }
  .card--front { top: 106px; background: var(--white); }
  .card--back { top: 640px; background: var(--navy); }

  .wordmark {
    position: absolute;
    display: flex;
    align-items: center;
    gap: 16px;
    line-height: 1;
    white-space: nowrap;
  }
  .wordmark__dot {
    border-radius: 50%;
    flex: none;
  }
  .card--front .wordmark {
    right: 46px;
    top: 62px;
    font-size: 56px;
    font-weight: 700;
    letter-spacing: 1px;
    color: var(--navy);
  }
  .card--front .wordmark__dot {
    width: 60px; height: 60px;
    background: var(--navy);
  }
  .card--back .wordmark {
    left: 50%; top: 50%;
    transform: translate(-50%, -50%);
    font-size: 68px;
    font-weight: 400;
    letter-spacing: 1px;
    color: var(--silver);
  }
  .card--back .wordmark__dot {
    width: 88px; height: 88px;
    background: var(--silver);
  }

  .contact {
    position: absolute;
    left: 48px;
    top: 286px;
    width: 732px;
  }
  .contact__name {
    font-size: 27px;
    font-weight: 600;
    color: var(--navy);
    padding-bottom: 8px;
    border-bottom: 1.5px solid var(--rule);
  }
  .contact__row {
    display: flex;
    align-items: center;
    gap: 12px;
    font-size: 18px;
    font-weight: 600;
    color: var(--ink);
    margin-top: 4px;
  }
  .contact__row:first-of-type { margin-top: 14px; }
  .contact__icon { width: 18px; height: 18px; fill: var(--navy); flex: none; }
  .contact__row--email { font-size: 16px; font-weight: 500; }

  .footer-bands { position: absolute; left: 0; bottom: 0; width: 825px; height: 60px; }
  .footer__web {
    position: absolute;
    right: 44px;
    bottom: 14px;
    color: var(--white);
    font-size: 16px;
    font-weight: 600;
    letter-spacing: 4px;
  }
</style>
</head>
<body>
  <section class="card card--front">
    <div class="wordmark">HARTVALE<span class="wordmark__dot"></span></div>

    <div class="contact">
      <p class="contact__name">Garrick Tenwood</p>
      <p class="contact__row">
        <svg class="contact__icon" viewBox="0 0 24 24"><path d="M6.6 10.8a15.2 15.2 0 0 0 6.6 6.6l2.2-2.2a1 1 0 0 1 1-.25 11.4 11.4 0 0 0 3.6.57 1 1 0 0 1 1 1V20a1 1 0 0 1-1 1A17 17 0 0 1 3 4a1 1 0 0 1 1-1h3.5a1 1 0 0 1 1 1c0 1.25.2 2.45.57 3.570a1 1 0 0 1-.25 1z"/></svg>
        0275390628
      </p>
      <p class="contact__row contact__row--email">
        <svg class="contact__icon" viewBox="0 0 24 24"><path d="M2 5h20v14H2zm2 2v.4l8 5.2 8-5.2V7zm0 2.8V17h16V9.8l-8 5.2z"/></svg>
        garrickt@hartvale.co.nz
      </p>
    </div>

    <svg class="footer-bands" viewBox="0 0 825 60" preserveAspectRatio="none">
      <polygon points="0,14 492,18 478,32 0,32" fill="var(--orange)"/>
      <polygon points="0,38 476,38 520,2 825,2 825,60 0,60" fill="var(--navy)"/>
    </svg>
    <p class="footer__web">www.hartvale.co.nz</p>
  </section>

  <section class="card card--back">
    <div class="wordmark">HARTVALE<span class="wordmark__dot"></span></div>
  </section>
</body>
</html>
```